Packaging Design: Logo/Bottle Design for New Garden Spritzer Brand

We are a new start up, looking to create a new line of Ready to drink Cocktails. The brand name is Verdance Garden Spritzers, infused with fruit, herb, and floral botanicals grown on our farm in New Hampshire. Flavors will include: Herb flavored with cilantro, Berry- flavored with Ridgeglow Berry, Citrus flavored with lemon Verbena & lemon balm, Pear flavored with Quillon pear, Cucumber & Mint. We need a logo and a label design. There are 2 possible bottles to choose from.

Designer has complete freedom with everything! From fonts and colors to bottle caps and closures. Please view the pinterest link for inspirational bottle designs. https://www.pinboardia.com/dellacravitz/garden-spritzers/

Reason: I am extending the deadline for my project to allow more designers to submit their designs.

Target Market(s)

Female 21 to 48 years old. College educated and professional. The type of person that has a passion for a cause and eats and shops local. People that respect an artisan quality product, hand made by a master craftsman.

Industry/Entity Type

Floral

Requirements
Must have
• Clear Bottle, see options attached. You may also choose your own BUT WE MUST SEE THE LOGO AND IMAGERY ON A BOTTLE
• Logo Design: "Verdance Garden Spritzers"
• Label: We can have front and back, or one continuous label. We are open to painted designs.
• The label must contain the following text in quotes:
• Product Name: " Verdance Garden Spritzers "
• "15% Alc. by Vol. (30 proof)"
• "750 mL"
• "Handcrafted and Bottled by Hollowmere Stillbrook Farm and Distillery
• Winchester, NH-USA"
• The following Text must be in all caps and 3mm in height:
• "Government Warning: (1) According to the Surgeon General, women should not drink alcoholic beverages during pregnancy because of the risk of birth defects. (2) Consumption of alcoholic beverages impairs your ability to drive a car or operate machinery and may cause health problems."
• Must be a space for a bar code: .75 in height by 1.25 in length.
• “www.hollowmerestillbrook.com”
• Must Have the following Statement:
• Infused with fruit, herb, and floral botanicals and sweetened with stevia. Serve cold over ice.
Nice to have
• Antique or vintage botanical illustrations
• https://www.pinboardia.com/dellacravitz/garden-spritzers/
• check out the board for inspiration.
• Think artisanal small batch spirits that are ready to drink out of the bottle. Refreshing flavors just pour over ice and add herb leaves.
• You can use images by doing a search here.
• http://archv.plantrec.example.org/archv/search.xhtml?start=0&collectionFacet=Orchard+Painted+Plate+Archive

```html
<!DOCTYPE html>
<html lang="en">
<head>
<meta charset="utf-8">
<title>Verdance Garden Spritzers – Pear Bottle</title>
<link rel="stylesheet" href="https://fonts.googleapis.com/css2?family=Libre+Baskerville&display=swap">
<style>
  :root {
    --bg-top: #5a2629;
    --bg-mid: #030102;
    --bg-bottom: #1a0305;
    --glass: #1c0709;
    --glass-deep: #0f0304;
    --glass-edge: #4a3c3e;
    --glass-shine: #6a5a5c;
    --cap: #0d0b0c;
    --base-glass: #3b3536;
    --label-paper: #f4f4f4;
    --label-edge: #d6d6d6;
    --ink: #111111;
    --ribbon-light: #c4c1bb;
    --ribbon-dark: #8c8984;
    --ribbon-text: #ffffff;
    --art-green: #6d8445;
    --art-leaf: #3c4a2c;
    --art-blush: #b7563f;
  }
  * { box-sizing: border-box; margin: 0; padding: 0; }
  html, body { width: 1200px; height: 2250px; overflow: hidden; }
  body {
    position: relative;
    background: linear-gradient(180deg, var(--bg-top) 0%, var(--bg-mid) 42%, var(--bg-mid) 72%, var(--bg-bottom) 100%);
    font-family: "Libre Baskerville", "Times New Roman", serif;
  }
  .bottle-scene { position: absolute; left: 0; top: 0; width: 1200px; height: 2250px; }
  .label-text {
    position: absolute;
    left: 483px; width: 240px;
    text-align: center;
    color: var(--ink);
    white-space: nowrap;
  }
  .brand-name { top: 1132px; font-size: 34px; line-height: 46px; letter-spacing: 1px; }
  .product-line { top: 1252px; font-size: 26px; line-height: 42px; }
  .fruit-illustration {
    position: absolute;
    left: 508px; top: 1345px;
    width: 190px; height: 235px;
    border-radius: 18px;
    background: radial-gradient(ellipse at 50% 65%, var(--art-green) 0%, var(--art-leaf) 55%, var(--art-blush) 100%);
    opacity: 0.55;
  }
  .flavour-name { top: 1598px; font-size: 36px; line-height: 46px; }
  .ribbon-text {
    position: absolute;
    left: 562px; top: 372px;
    width: 76px;
    writing-mode: vertical-rl;
    text-orientation: upright;
    font-size: 21px;
    letter-spacing: 15px;
    line-height: 76px;
    color: var(--ribbon-text);
  }
</style>
</head>
<body>
  <svg class="bottle-scene" viewBox="0 0 1200 2250" aria-hidden="true">
    <defs>
      <linearGradient id="glassBody" x1="0" x2="1" y1="0" y2="0">
        <stop offset="0" stop-color="var(--glass-edge)"/>
        <stop offset="0.06" stop-color="var(--glass)"/>
        <stop offset="0.5" stop-color="var(--glass-deep)"/>
        <stop offset="0.94" stop-color="var(--glass)"/>
        <stop offset="1" stop-color="var(--glass-edge)"/>
      </linearGradient>
      <linearGradient id="ribbonSheen" x1="0" x2="1" y1="0" y2="0">
        <stop offset="0" stop-color="var(--ribbon-dark)"/>
        <stop offset="0.5" stop-color="var(--ribbon-light)"/>
        <stop offset="1" stop-color="var(--ribbon-dark)"/>
      </linearGradient>
    </defs>
    <!-- bottle glass -->
    <path class="bottle-glass" fill="url(#glassBody)"
      d="M520 300 L520 520 C520 620 446 640 446 720 L446 2085 Q446 2108 470 2108 L734 2108 Q758 2108 758 2085 L758 720 C758 640 684 620 684 520 L684 300 Z"/>
    <path class="bottle-base" fill="var(--base-glass)" opacity="0.8"
      d="M446 2012 L758 2012 L758 2085 Q758 2108 734 2108 L470 2108 Q446 2108 446 2085 Z"/>
    <rect class="glass-highlight" x="462" y="740" width="6" height="1250" fill="var(--glass-shine)" opacity="0.45"/>
    <rect class="glass-highlight" x="736" y="740" width="5" height="1250" fill="var(--glass-shine)" opacity="0.35"/>
    <!-- capsule -->
    <rect class="bottle-cap" x="512" y="213" width="181" height="122" rx="8" fill="var(--cap)"/>
    <!-- oval label -->
    <ellipse class="label-oval" cx="603" cy="1338" rx="120" ry="442" fill="var(--label-paper)" stroke="var(--label-edge)" stroke-width="2"/>
    <!-- neck ribbon -->
    <polygon class="neck-ribbon" points="562,219 638,219 638,1020 600,962 562,1020" fill="url(#ribbonSheen)"/>
  </svg>

  <div class="ribbon-text">QUILLON PEAR</div>
  <div class="label-text brand-name">VERDANCE</div>
  <div class="label-text product-line">GARDEN<br>SPRITZER</div>
  <div class="fruit-illustration" role="img" aria-label="Vintage botanical illustration of a pear on a leafy branch"></div>
  <div class="label-text flavour-name">PEAR</div>
</body>
</html>
```